Tessmar Fahrwerkstatt
Sehr angenehme zusammenarbeit nicht aufdringlich und genau auf die Wünsche eingegangen. Wir werde sicher noch mehr zusammen Arbeiten. Gruss Lukas Hegemann Inhaber Tessmar Fahrwerkstatt
Zielgruppe
Dinks und Kunden mit viel Erfolg und hohem Ausgabepotential.
Aufgabenstellung
Unsere Firma vertreibt Fahrzeuge im Luxusbereich hauptgebiet Valmerra aber auch andere Sportwagen. Was uns fehlt ist ein optischer Wiedererkennugswert. Deshalb hätten wir gerne ein Visitenkarten Design und Briefpapier Design. Später soll auch noch eine Webseite mit gleichem Wiedererkennungswert entstehen. " Roter Faden "

```html
<!DOCTYPE html>
<html lang="de">
<head>
<meta charset="utf-8">
<title>Tessmar Fahrwerkstatt – Visitenkarte</title>
<link rel="stylesheet" href="https://fonts.googleapis.com/css2?family=Alegreya+Sans:wght@400;700&display=swap">
<style>
  :root {
    --backdrop: #e9e6e1;
    --navy-deep: #101a3c;
    --navy-mid: #1b2a5c;
    --navy-glow: #2a3d78;
    --gold-light: #f3d79a;
    --gold: #d6a852;
    --gold-dark: #a87a2e;
    --ink-gold: #c9a06b;
    --card-size: 416px;
    --corner: 48px;
  }
  * { box-sizing: border-box; margin: 0; padding: 0; }
  html, body {
    width: 1200px;
    height: 800px;
    overflow: hidden;
    background: var(--backdrop);
    font-family: "Alegreya Sans", "Trebuchet MS", sans-serif;
  }
  .stage {
    position: relative;
    width: 1200px;
    height: 800px;
  }
  .card {
    position: absolute;
    top: 192px;
    width: var(--card-size);
    height: var(--card-size);
  }
  .card--front { left: 137px; }
  .card--back { left: 649px; }

  .card__corner {
    position: absolute;
    width: var(--corner);
    height: var(--corner);
    background: linear-gradient(135deg, var(--gold-light) 0%, var(--gold) 45%, var(--gold-dark) 100%);
  }
  .card__corner--tl { top: 0; left: 0; }
  .card__corner--tr { top: 0; right: 0; }
  .card__corner--bl { bottom: 0; left: 0; }
  .card__corner--br { bottom: 0; right: 0; }

  .card__face {
    position: absolute;
    inset: 0;
    background:
      radial-gradient(ellipse 70% 55% at 50% 52%, var(--navy-glow) 0%, var(--navy-mid) 45%, var(--navy-deep) 100%);
    clip-path: polygon(
      var(--corner) 0, calc(100% - var(--corner)) 0,
      calc(100% - var(--corner)) var(--corner), 100% var(--corner),
      100% calc(100% - var(--corner)), calc(100% - var(--corner)) calc(100% - var(--corner)),
      calc(100% - var(--corner)) 100%, var(--corner) 100%,
      var(--corner) calc(100% - var(--corner)), 0 calc(100% - var(--corner)),
      0 var(--corner), var(--corner) var(--corner)
    );
  }
  .card__gloss {
    position: absolute;
    inset: 0;
    background: radial-gradient(ellipse 120% 60% at 40% 0%, rgba(255,255,255,0.10) 0%, rgba(255,255,255,0.05) 60%, rgba(255,255,255,0) 61%);
  }

  .brand {
    position: absolute;
    left: 0;
    right: 0;
    top: 190px;
    text-align: center;
    color: var(--gold);
    font-weight: 400;
    font-size: 26px;
    line-height: 30px;
    letter-spacing: 0.12em;
    text-transform: uppercase;
  }

  .contact {
    position: absolute;
    left: 0;
    right: 0;
    top: 86px;
    text-align: center;
    color: var(--ink-gold);
    font-size: 19px;
    line-height: 26px;
  }
  .contact__person { font-weight: 700; }
  .contact__web { margin-top: 22px; }
  .contact__address { margin-top: 25px; }
</style>
</head>
<body>
  <main class="stage">
    <section class="card card--front" aria-label="Vorderseite der Visitenkarte">
      <div class="card__corner card__corner--tl"></div>
      <div class="card__corner card__corner--tr"></div>
      <div class="card__corner card__corner--bl"></div>
      <div class="card__corner card__corner--br"></div>
      <div class="card__face">
        <div class="card__gloss"></div>
        <p class="brand">Tessmar<br>Fahrwerkstatt</p>
      </div>
    </section>

    <section class="card card--back" aria-label="Rückseite der Visitenkarte">
      <div class="card__corner card__corner--tl"></div>
      <div class="card__corner card__corner--tr"></div>
      <div class="card__corner card__corner--bl"></div>
      <div class="card__corner card__corner--br"></div>
      <div class="card__face">
        <div class="card__gloss"></div>
        <div class="contact">
          <p class="contact__person">Lukas Hegemann<br>Tel.: +41 79 512 38 64</p>
          <p class="contact__web">info@tessmar.ch | www.tessmar.ch</p>
          <p class="contact__address">Büro: Lindenhofweg 14<br>CH 8183 Talwil</p>
          <p class="contact__address">Showroom: Mühlegasse 22<br>CH 8617 Rebhalden</p>
        </div>
      </div>
    </section>
  </main>
</body>
</html>
```